velorahelp Web Design Project

It is a virtual assistance/concierge company that helps the busy professional by remotely providing administrative, technical and/or creative business support services, specializing in the medical device industry. Company name is velorahelp.
(website will be velorahelp.example)

Allowing things to be done without taking time away from more urgent issues or family/personal time. Partnering with a VA reduces stress, protects cash flow, eliminates administrative hassles, and enables business people to find the success they originally set out to achieve. Saves small businesses and/or individuals on overhead, salary, et. Work is done remotely to offer administrative, clerical, typing and specialist service assistance on a regular, ad-hoc or emergency cover basis.

Though we are capable of addressing the needs of medical professionals and industry representatives due to our experience and knowledge (sales, HCC guidelines, etc.) we do not want to be limited to that market only.

Target Market(s)

Target market would be M/F, 30-50, National, busy, Alpha, entrepreneurs and industry professionals who want/need to do more without sacrifice of life

Requirements
Nice to have
• We do have a logo designed via the PlanMarket website that can/should be included. Logo is uploaded.

```html
<!DOCTYPE html>
<html lang="en">
<head>
<meta charset="utf-8">
<title>velorahelp</title>
<link rel="stylesheet" href="https://fonts.googleapis.com/css2?family=Open+Sans:wght@400;600;700&family=Gelasio:ital,wght@1,400;1,700&display=swap">
<style>
  :root {
    --sky: #56cdf0;
    --nav: #0b7a94;
    --nav-edge: #066b83;
    --nav-active: #7fe0ff;
    --teal: #0a7590;
    --ink: #333333;
    --navy: #16324f;
    --footer: #073f51;
    --footer-text: #a9d4e0;
    --line: #d8d8d8;
    --white: #ffffff;
  }
  * { box-sizing: border-box; margin: 0; padding: 0; }
  html, body { width: 722px; height: 1200px; overflow: hidden; }
  body {
    position: relative;
    background: var(--white);
    font-family: "Open Sans", Verdana, sans-serif;
    color: var(--ink);
  }
  .abs { position: absolute; }

  /* header */
  .site-header { left: 0; top: 0; width: 722px; height: 91px; background: var(--sky); }
  .brand { left: 74px; top: 28px; display: flex; align-items: center; gap: 6px; }
  .brand-dot { width: 14px; height: 14px; border-radius: 50%; background: var(--navy); }
  .brand-name { font-weight: 700; font-size: 33px; color: var(--navy); letter-spacing: -0.5px; line-height: 1; }
  .hotline { right: 71px; top: 27px; font-size: 12px; color: var(--white); }
  .search { left: 518px; top: 51px; width: 134px; height: 24px; background: var(--white); border-radius: 3px;
            font-size: 11px; color: #777; padding: 5px 7px; }
  .search svg { position: absolute; right: 7px; top: 5px; }

  .main-nav { left: 0; top: 91px; width: 722px; height: 44px; background: var(--nav); border-top: 2px solid var(--nav-edge); }
  .main-nav a { position: absolute; top: 14px; font-size: 13px; color: var(--white); text-decoration: none; transform: translateX(-50%); }
  .main-nav a.active { color: var(--nav-active); }

  /* hero */
  .hero { left: 74px; top: 153px; width: 578px; height: 241px;
          background: linear-gradient(90deg, #6e5a48 0%, #b99a7c 35%, #d8c3ac 60%, #c49a74 100%);
          box-shadow: 0 2px 5px rgba(0,0,0,0.45); }
  .dots { left: 346px; top: 406px; display: flex; gap: 3px; }
  .dots span { width: 8px; height: 8px; border-radius: 50%; background: #8c8c8c; }
  .dots span.on { background: #2a7fc0; }

  /* feature columns */
  .feature { width: 180px; }
  .feature h3 { font-family: "Gelasio", Georgia, serif; font-style: italic; font-weight: 700; font-size: 13px;
                color: #222; text-align: center; height: 24px; }
  .feature .thumb { height: 104px; border: 1px solid #cfcfcf; box-shadow: 0 1px 3px rgba(0,0,0,0.25); }
  .feature p { margin-top: 18px; font-size: 12px; line-height: 16px; padding-left: 1px; }
  .more-btn { display: block; width: 51px; height: 25px; border: 1px solid #c9c9c9; border-radius: 4px;
              background: linear-gradient(#ffffff, #f0f0f0); font-size: 11px; color: var(--teal);
              text-align: center; line-height: 23px; box-shadow: 0 1px 2px rgba(0,0,0,0.2); }
  .feature .more-btn { margin-top: 11px; }

  .section-title { font-family: "Gelasio", Georgia, serif; font-style: italic; font-size: 14px; color: #333; }
  .section-title b { color: var(--teal); font-weight: 700; }

  .welcome { left: 76px; top: 737px; width: 370px; }
  .welcome p { margin-top: 8px; font-size: 12px; line-height: 20px; }
  .welcome .more-btn { margin-top: 13px; margin-left: -1px; }

  .services { left: 465px; top: 737px; width: 187px; }
  .services ul { list-style: none; margin-top: 7px; }
  .services li { display: flex; align-items: center; gap: 9px; font-size: 12px; height: 24.5px; }
  .services li i { width: 15px; height: 15px; border-radius: 50%; border: 1px solid #c8c8c8;
                   background: radial-gradient(#ffffff, #e6e6e6); position: relative; }
  .services li i::after { content: ""; position: absolute; left: 5px; top: 3.5px;
                          border-left: 5px solid var(--teal); border-top: 3.5px solid transparent; border-bottom: 3.5px solid transparent; }
  .services .more-btn { margin-top: 12px; }

  /* clients */
  .clients { left: 74px; top: 959px; width: 578px; height: 155px; border: 1px solid #d6d6d6; border-radius: 4px;
             box-shadow: 0 1px 4px rgba(0,0,0,0.25); }
  .clients .section-title { position: absolute; left: 11px; top: 8px; }
  .clients .rule { position: absolute; left: 10px; right: 13px; top: 30px; border-top: 1px solid var(--line); }
  .clients .arrows { position: absolute; right: 16px; top: 8px; display: flex; gap: 4px; }
  .clients .arrows i { width: 14px; height: 14px; border-radius: 50%; border: 1px solid #c4c4c4; background: #f4f4f4; position: relative; }
  .clients .arrows i.prev::after { content: ""; position: absolute; left: 3px; top: 3px;
        border-right: 5px solid var(--teal); border-top: 3.5px solid transparent; border-bottom: 3.5px solid transparent; }
  .clients .arrows i.next::after { content: ""; position: absolute; left: 5px; top: 3px;
        border-left: 5px solid var(--teal); border-top: 3.5px solid transparent; border-bottom: 3.5px solid transparent; }
  .client { position: absolute; top: 41px; width: 125px; }
  .client .thumb { height: 74px; border: 1px solid #bdbdbd;
                   background: linear-gradient(90deg, #9aa3a0 0%, #d9b49a 45%, #c89b7e 70%, #a7aca8 100%); }
  .client span { display: block; margin-top: 10px; padding-left: 3px; font-family: "Gelasio", Georgia, serif;
                 font-style: italic; font-size: 10px; color: #444; }

  /* footer */
  .site-footer { left: 0; top: 1134px; width: 722px; height: 66px; background: var(--footer); }
  .footer-info { left: 77px; top: 8px; font-size: 8.5px; line-height: 11px; color: var(--footer-text); }
  .footer-info strong { display: block; font-family: "Gelasio", Georgia, serif; font-style: italic; font-size: 12px;
                        color: var(--white); text-decoration: underline; line-height: 14px; }
  .find-us { left: 530px; top: 16px; display: flex; align-items: center; gap: 5px; font-size: 8.5px; color: var(--footer-text); }
  .find-us i { width: 14px; height: 14px; border-radius: 3px; background: #2f86b5; display: block; }
  .copyright { left: 515px; top: 38px; font-size: 8.5px; color: var(--footer-text); }
</style>
</head>
<body>

<header class="abs site-header">
  <div class="abs brand"><span class="brand-dot"></span><span class="brand-name">velorahelp</span></div>
  <div class="abs hotline">Call us @ 1800 - 55 - 010203</div>
  <div class="abs search">search...
    <svg width="13" height="13" viewBox="0 0 13 13"><circle cx="5" cy="5" r="3.8" fill="none" stroke="#888" stroke-width="1.6"/><line x1="8" y1="8" x2="12" y2="12" stroke="#888" stroke-width="2"/></svg>
  </div>
</header>

<nav class="abs main-nav">
  <a class="active" style="left:143px">Home</a>
  <a style="left:268px">About Us</a>
  <a style="left:415px">Our Services</a>
  <a style="left:564px">Contact Us</a>
</nav>

<div class="abs hero" role="img" aria-label="Photo of a smiling call-centre assistant with a headset in front of a hospital imaging room"></div>
<div class="abs dots"><span class="on"></span><span></span><span></span><span></span></div>

<section class="abs feature" style="left:74px; top:451px;">
  <h3>Recieving calls</h3>
  <div class="thumb" role="img" aria-label="Photo of an assistant with a headset in an office" style="background:linear-gradient(90deg,#5b6b78,#b09680 60%,#e5d7c8);"></div>
  <p>Put here something about collection of client query or calls to researching over them in a brief.</p>
  <span class="more-btn">More</span>
</section>
<section class="abs feature" style="left:273px; top:451px;">
  <h3>Reserching Issues</h3>
  <div class="thumb" role="img" aria-label="Photo of a man working at computer monitors" style="background:linear-gradient(90deg,#4d5e6e,#8d9eae 45%,#c49f86 75%,#6a7a8c);"></div>
  <p>Put here something about researching of client query or calls to researching over them in a brief.</p>
  <span class="more-btn">More</span>
</section>
<section class="abs feature" style="left:471px; top:451px;">
  <h3>Resolving Problems</h3>
  <div class="thumb" role="img" aria-label="Photo of a business handshake" style="background:linear-gradient(135deg,#2c3a55,#9bbad6 50%,#e8eef4);"></div>
  <p>Put here something about resolving of client query or calls to researching over them in a brief.</p>
  <span class="more-btn">More</span>
</section>

<section class="abs welcome">
  <h2 class="section-title"><b>Welcome</b> to our site</h2>
  <p>It is a virtual assistance/concierge company that helps the busy professional by remotely providing administrative, technical and/or creative business support services, specializing in the medical device industry. Company name is velorahelp. It is a virtual assistance/concierge company that helps the busy professional by remotely providing administrative, technical and/or creative business support services.</p>
  <span class="more-btn">More</span>
</section>

<section class="abs services">
  <h2 class="section-title"><b>Our</b> Services</h2>
  <ul>
    <li><i></i>Service goes here</li>
    <li><i></i>Service goes here</li>
    <li><i></i>Service goes here</li>
    <li><i></i>Service goes here</li>
    <li><i></i>Service goes here</li>
    <li><i></i>Service goes here</li>
  </ul>
  <span class="more-btn">More</span>
</section>

<section class="abs clients">
  <h2 class="section-title"><b>Our</b> Clients</h2>
  <div class="arrows"><i class="prev"></i><i class="next"></i></div>
  <div class="rule"></div>
  <div class="client" style="left:10px"><div class="thumb" role="img" aria-label="Client photo"></div><span>Maplecrest Clinic</span></div>
  <div class="client" style="left:154px"><div class="thumb" role="img" aria-label="Client photo"></div><span>Maplecrest Clinic</span></div>
  <div class="client" style="left:298px"><div class="thumb" role="img" aria-label="Client photo"></div><span>Maplecrest Clinic</span></div>
  <div class="client" style="left:439px"><div class="thumb" role="img" aria-label="Client photo"></div><span>Maplecrest Clinic</span></div>
</section>

<footer class="abs site-footer">
  <div class="abs footer-info">
    <strong>velorahelp</strong>
    Emergency Call : 1800-00-0455<br>
    Fax : 6510000199<br>
    E-mail : help4@velorahelp.example
  </div>
  <div class="abs find-us">Find Us :&nbsp; <i></i><i></i><i></i></div>
  <div class="abs copyright">Copyright 2012 | Privacy Policy</div>
</footer>

</body>
</html>
```